Business Card Design for Training Business

Clear Path Coaching is a new business that delivers training and other services with a focus on topics related to mental health and wellbeing, for example, Wellmind Response Course, Resilience etc. We have a strong focus on evidence-based psychology and neuroscience. I have a logo which I will upload with the brief, so please consider colours that work well with the logo.
Target Market(s)
Adults, workplaces (particularly government and not-for-profits)
Industry/Entity Type
Business
Contact Information for Business Card
Head Strong TrainingSamantha SellwoodDirector0438 770 850sam@headstrongtraining.com.auwww.headstrongtraining.com.au

```html
<!DOCTYPE html>
<html lang="en">
<head>
<meta charset="utf-8">
<title>Clear Path Coaching – Business Card</title>
<link rel="stylesheet" href="https://fonts.googleapis.com/css2?family=Questrial&display=swap">
<style>
  :root {
    --backdrop: #3a3a3a;
    --card: #f7f7f7;
    --teal: #22b5bb;
    --teal-light: #3cc3c6;
    --swoosh-grey: #8a8a8a;
    --ink: #4a4a4a;
    --ink-soft: #6d6d6d;
  }
  * { box-sizing: border-box; margin: 0; padding: 0; }
  html, body {
    width: 1200px; height: 750px; overflow: hidden;
    background: var(--backdrop);
    font-family: "Questrial", "Century Gothic", sans-serif;
  }
  .stage { position: relative; width: 1200px; height: 750px; }
  .card {
    position: absolute; left: 371px; width: 461px; height: 263px;
    background: var(--card); border-radius: 14px; overflow: hidden;
  }
  .card--front { top: 106px; }
  .card--back { top: 388px; }
  .swooshes { position: absolute; inset: 0; }

  .brand {
    position: absolute; top: 22px; right: 24px; width: 160px;
    display: flex; flex-direction: column; align-items: center;
  }
  .brand__dot {
    width: 58px; height: 58px; border-radius: 50%;
    border: 2px solid var(--teal);
  }
  .brand__name {
    margin-top: 12px; font-size: 13px; letter-spacing: 2.4px;
    text-transform: uppercase; color: var(--ink-soft); white-space: nowrap;
  }

  .person { position: absolute; left: 24px; top: 148px; }
  .person__name { font-size: 19px; color: var(--teal); line-height: 1.1; }
  .person__role { font-size: 14px; color: var(--ink); margin-top: 2px; }

  .contacts { position: absolute; left: 25px; top: 199px; list-style: none; }
  .contacts li {
    display: flex; align-items: center; gap: 6px;
    font-size: 12px; color: var(--ink); height: 17.5px;
  }
  .contacts svg { width: 12px; height: 12px; flex: none; }

  .back-brand {
    position: absolute; top: 74px; left: 0; right: 0;
    display: flex; flex-direction: column; align-items: center;
  }
  .back-brand__dot {
    width: 110px; height: 110px; border-radius: 50%;
    border: 2px solid var(--teal);
    display: flex; align-items: center; justify-content: center;
  }
  .back-brand__name {
    font-size: 11px; letter-spacing: 1.6px; text-transform: uppercase;
    color: var(--teal); text-align: center; line-height: 1.5;
  }
  .back-url {
    position: absolute; left: 0; right: 0; top: 226px;
    text-align: center; font-size: 12.5px; color: var(--ink);
  }
</style>
</head>
<body>
<main class="stage">

  <section class="card card--front" aria-label="Card front">
    <svg class="swooshes" viewBox="0 0 461 263" aria-hidden="true">
      <path d="M0 0 H102 C55 20 15 60 0 105 Z" fill="var(--teal)"/>
      <path d="M103 1 C55 22 14 62 3 108" fill="none" stroke="var(--swoosh-grey)" stroke-width="2.5"/>
      <path d="M461 160 C440 205 400 240 355 263 H461 Z" fill="var(--teal)"/>
      <path d="M459 160 C440 205 398 238 352 262" fill="none" stroke="var(--swoosh-grey)" stroke-width="2.5"/>
    </svg>

    <div class="brand">
      <span class="brand__dot"></span>
      <span class="brand__name">Clear Path Coaching</span>
    </div>

    <div class="person">
      <h1 class="person__name">Rebecca Tanfield</h1>
      <p class="person__role">Director</p>
    </div>

    <ul class="contacts">
      <li>
        <svg viewBox="0 0 12 12" aria-hidden="true"><path d="M2.5 1 L4.3 1 L5 3.5 L3.8 4.4 C4.5 6 5.8 7.3 7.5 8.1 L8.4 7 L11 7.6 L11 9.5 C11 10.3 10.4 11 9.6 11 C5 10.6 1.2 6.8 1 2.3 C1 1.6 1.7 1 2.5 1 Z" fill="var(--teal)"/></svg>
        0491 362 517
      </li>
      <li>
        <svg viewBox="0 0 12 12" aria-hidden="true"><rect x="0.5" y="2.5" width="11" height="7.5" fill="var(--teal)"/><path d="M0.8 2.8 L6 7 L11.2 2.8" fill="none" stroke="#fff" stroke-width="0.9"/></svg>
        bec@clearpathcoaching.example.au
      </li>
      <li>
        <svg viewBox="0 0 12 12" aria-hidden="true"><circle cx="6" cy="6" r="5.5" fill="var(--teal)"/><path d="M3 3.5 C4.5 3 5 4.5 4 5.5 C3.2 6.3 4.5 7.5 5 9 M7.5 2 C7 3.5 8.5 4 9.5 4.5 M8 7 C7.5 8 8 9 8.8 9.2" fill="none" stroke="#fff" stroke-width="0.9"/></svg>
        www.clearpathcoaching.example.au
      </li>
    </ul>
  </section>

  <section class="card card--back" aria-label="Card back">
    <div class="back-brand">
      <div class="back-brand__dot">
        <span class="back-brand__name">Clear Path<br>Coaching</span>
      </div>
    </div>
    <p class="back-url">www.clearpathcoaching.example.au</p>
  </section>

</main>
</body>
</html>
```